Basic / Quick Business Card

Quick easy design project!

Need a one sided basic business card that matches font & style of brand and bottle label for our gourmet condiment, Brindle Harrow Sauce. Brindle Harrow Sauce is sold in specialty retail, gourmet groceries and appears on chef-driven restaurant menus, so the target market is a high end, gourmet, artisan-made food-loving customer.

Files Included:
Sauce Bottle Label
Brindle Harrow Sauce Round Logos

**About the logos - the logo may be used in a circle or alone vertically as on side of the bottle label**

Layout of Card:
May be vertical or horizontal based on designer ideas.

Logo usage (in circle vs. stand alone vertical logo) is up to designers descretion as well.

Reverse side of business card will be various high end / professional product photos / food shots using us.kelbo.com system. **Designer on this project will NOT design a reserve for the card.**

Paper that will be used for printing:
Kelbo Standard - it's a WHITE paper, but we use a cream background on Brindle Harrow Sauce branding, so please take this into account on design to stay brand consistent.

Elements & Copy for Card:
1. Logo in either script horizontal or vertical version
2. Copy: "Artisan Made - Small Batch"
3. Name - Wes Dorrance
4. Title - Creator
5. Phone - xxx.xxx.xxxx
6. xxxx@brindleharrow.com
7. URL: brindleharrowsauce.com
8. Social Media: @getbrindleharrow on Quillo / Pagora / Lumigrid

Please provide final files in Illustrator or InDesign format.

```html
<!DOCTYPE html>
<html lang="en">
<head>
<meta charset="utf-8">
<title>Brindle Harrow Sauce – Business Card</title>
<link href="https://fonts.googleapis.com/css2?family=Crimson+Text:wght@400&family=Open+Sans:wght@400&display=swap" rel="stylesheet">
<style>
  :root {
    --page: #e9e6e1;
    --metal-light: #f4f5f6;
    --metal-mid: #d9dbdd;
    --metal-dark: #c3c6c9;
    --ink: #2b2624;
    --pill: #2e2a27;
    --gold: #e0a82a;
    --cream: #f3eed6;
  }
  * { margin: 0; padding: 0; box-sizing: border-box; }
  html, body {
    width: 1200px; height: 749px; overflow: hidden;
    background: var(--page);
  }
  .card {
    position: absolute; left: 40px; top: 54px;
    width: 1120px; height: 641px;
    border-radius: 46px;
    background:
      repeating-linear-gradient(0deg, rgba(255,255,255,0.18) 0 1px, rgba(0,0,0,0.025) 1px 3px),
      linear-gradient(115deg, var(--metal-mid) 0%, var(--metal-light) 38%, var(--metal-dark) 62%, var(--metal-light) 85%, var(--metal-mid) 100%);
    box-shadow: 0 4px 14px rgba(0,0,0,0.18);
    font-family: "Crimson Text", Georgia, serif;
    color: var(--ink);
  }
  .brand-mark {
    position: absolute; left: 88px; top: 95px;
    width: 292px; height: 292px; border-radius: 50%;
    background: var(--cream);
    display: flex; align-items: center; justify-content: center;
    text-align: center;
  }
  .brand-name {
    font-size: 44px; line-height: 1.05; color: var(--ink);
  }
  .tagline, .contact {
    position: absolute; right: 120px; text-align: right;
    font-size: 28px; line-height: 32px;
  }
  .tagline { top: 125px; }
  .contact { top: 262px; line-height: 40px; }
  .contact li { list-style: none; display: flex; justify-content: flex-end; align-items: center; gap: 8px; }
  .contact svg { width: 24px; height: 24px; fill: var(--ink); }
  .name-pill {
    position: absolute; left: 100px; top: 472px;
    width: 337px; height: 103px; border-radius: 52px;
    background: var(--pill); color: var(--gold);
    padding: 14px 0 0 34px;
  }
  .person-name { font-size: 42px; line-height: 42px; }
  .person-title { font-size: 31px; line-height: 34px; }
  .social {
    position: absolute; right: 120px; top: 488px; text-align: right;
    font-family: "Open Sans", Arial, sans-serif;
  }
  .social-label { font-size: 31px; color: var(--ink); }
  .social-list { display: flex; gap: 16px; justify-content: flex-end; margin-top: 10px; list-style: none; }
  .social-list li { font-size: 20px; color: var(--ink); }
</style>
</head>
<body>
  <main class="card">
    <div class="brand-mark">
      <span class="brand-name">Brindle<br>Harrow<br>Sauce</span>
    </div>

    <p class="tagline">sweet &amp; spicy<br>made in mississippi<br>Artisan Made - Small Batch</p>

    <ul class="contact">
      <li>
        <svg viewBox="0 0 24 24" aria-hidden="true"><circle cx="12" cy="12" r="11" fill="none" stroke="currentColor" stroke-width="2" style="stroke:var(--ink)"/><path d="M8 6.5l2 0 1 3-1.4 1.2a7 7 0 0 0 3.7 3.7l1.2-1.4 3 1v2a1.5 1.5 0 0 1-1.6 1.5A10 10 0 0 1 6.5 8.1 1.5 1.5 0 0 1 8 6.5z"/></svg>
        123-456-7890
      </li>
      <li>
        <svg viewBox="0 0 24 24" aria-hidden="true"><path d="M2 8l10-5 10 5v12H2z"/><path d="M3.5 9.5l8.5 5 8.5-5" fill="none" stroke="#eee" stroke-width="1.6"/></svg>
        wdorrance@brindleharrow.com
      </li>
      <li>
        <svg viewBox="0 0 24 24" aria-hidden="true"><g fill="none" stroke="#2b2624" stroke-width="1.8"><circle cx="12" cy="12" r="10"/><ellipse cx="12" cy="12" rx="4.5" ry="10"/><path d="M2 12h20M4 7h16M4 17h16"/></g></svg>
        www.brindleharrowsauce.com
      </li>
    </ul>

    <div class="name-pill">
      <p class="person-name">Wes Dorrance</p>
      <p class="person-title">Creator</p>
    </div>

    <div class="social">
      <p class="social-label">Follow Us On</p>
      <ul class="social-list">
        <li>Pagora</li>
        <li>Quillo</li>
        <li>Lumigrid</li>
      </ul>
    </div>
  </main>
</body>
</html>
```